need corporate, modern business card created for Consulting Company

I need a slick business card using elements from my website, as well as, integrating my pixelforge-created logo (see files).

The business card needs to be:
1. Corporate and modern
2. Clean and professional

I've included a PSD with the logo/icon that you can use to create it. Feel free to try a metallic finish on the logo, make it bigger/small, underlay it. Whatever you need to do to make my card stand out.

Try a black background, or white background or gray.

The idea is for my card to be memorable as well as professional and corporate.

Target Market(s)

Corporate business in the US and Canada.

Industry/Entity Type

Business

Contact Information for Business Card

Commerce Advancing Methods
Martin Coles, Senior Partner
office: 1 877 555 0143
mobile: 1 519 555 0172
website: http://www.brightvale.example

Requirements
Must have
• Card-related information
• corporate, yet modern
• clean and professional
• incorporate the icon only
• must have an editable form when complete!
Nice to have
• metallic icon might be cool
• try it with white or black

```html
<!DOCTYPE html>
<html lang="en">
<head>
<meta charset="utf-8">
<title>Brightvale Business Card</title>
<link href="https://fonts.googleapis.com/css2?family=Open+Sans:wght@400;600;700&display=swap" rel="stylesheet">
<style>
  :root {
    --backdrop: #e4e6e9;
    --card-white: #ffffff;
    --card-shade: #eef0f2;
    --band-black: #1f2022;
    --brand-blue: #3b8ed6;
    --brand-blue-deep: #2a6fb8;
    --ink-dark: #222426;
    --ink-light: #ffffff;
    --rule-grey: #4a4d52;
  }
  html, body {
    margin: 0;
    padding: 0;
    width: 1200px;
    height: 885px;
    overflow: hidden;
    background: var(--backdrop);
    font-family: "Open Sans", Arial, sans-serif;
  }
  .canvas {
    position: relative;
    width: 1200px;
    height: 885px;
    display: flex;
    align-items: center;
    justify-content: center;
    gap: 40px;
  }
  .card {
    position: relative;
    width: 540px;
    height: 309px;
    border-radius: 16px;
    overflow: hidden;
    box-shadow: 0 10px 28px rgba(0,0,0,0.18);
    background: linear-gradient(180deg, var(--card-white) 0%, var(--card-shade) 100%);
  }

  /* Front card */
  .front__brand-zone {
    position: absolute;
    left: 0; top: 0;
    width: 100%;
    height: 150px;
  }
  .brand-lockup {
    position: absolute;
    left: 58px;
    top: 40px;
    display: flex;
    align-items: center;
    gap: 14px;
  }
  .brand-dot {
    width: 30px;
    height: 30px;
    border-radius: 50%;
    background: var(--brand-blue);
  }
  .brand-name {
    font-weight: 700;
    color: var(--brand-blue);
    font-size: 46px;
    letter-spacing: -1px;
    line-height: 1;
  }
  .front__tagline {
    position: absolute;
    left: 102px;
    top: 104px;
    font-size: 15px;
    font-weight: 600;
    color: var(--ink-dark);
  }
  .front__band {
    position: absolute;
    left: 0; top: 150px;
    width: 100%;
    height: 20px;
    background: var(--band-black);
  }
  .front__info-zone {
    position: absolute;
    left: 0; top: 170px;
    width: 100%;
    height: 139px;
    background: linear-gradient(180deg, var(--brand-blue-deep) 0%, var(--brand-blue) 55%, #4a9be0 100%);
    color: var(--ink-light);
  }
  .person {
    position: absolute;
    left: 58px;
    top: 12px;
    display: flex;
    align-items: center;
    gap: 10px;
    white-space: nowrap;
  }
  .person__name {
    font-size: 20px;
    font-weight: 700;
  }
  .person__divider {
    width: 1px;
    height: 20px;
    background: rgba(255,255,255,0.8);
  }
  .person__title {
    font-size: 16px;
    font-weight: 400;
  }
  .contact-list {
    position: absolute;
    left: 150px;
    top: 48px;
    margin: 0;
    padding: 0;
    list-style: none;
    font-size: 13px;
    line-height: 20px;
  }

  /* Back card */
  .back__lockup {
    position: absolute;
    left: 60px;
    top: 96px;
    display: flex;
    align-items: center;
    gap: 18px;
  }
  .back__lockup .brand-dot {
    width: 44px;
    height: 44px;
  }
  .back__lockup .brand-name {
    font-size: 72px;
    letter-spacing: -2px;
  }
  .back__web {
    position: absolute;
    left: 60px;
    top: 222px;
    display: flex;
    align-items: center;
    gap: 14px;
    font-size: 15px;
    font-weight: 600;
    color: var(--brand-blue);
  }
  .back__rule {
    width: 120px;
    height: 1px;
    background: var(--rule-grey);
  }
</style>
</head>
<body>
<main class="canvas">
  <section class="card card--front" aria-label="Card front">
    <div class="front__brand-zone">
      <div class="brand-lockup">
        <span class="brand-dot" aria-hidden="true"></span>
        <span class="brand-name">brightvale</span>
      </div>
      <div class="front__tagline">Commerce Advancing Methods</div>
    </div>
    <div class="front__band"></div>
    <div class="front__info-zone">
      <div class="person">
        <span class="person__name">Martin Coles</span>
        <span class="person__divider" aria-hidden="true"></span>
        <span class="person__title">Senior Partner</span>
      </div>
      <ul class="contact-list">
        <li>Phone: 1 877 555 0143</li>
        <li>Fax: 1 519 555 0172</li>
        <li>Web: www.brightvale.example</li>
        <li>E mail: info@brightvale.example</li>
      </ul>
    </div>
  </section>

  <section class="card card--back" aria-label="Card back">
    <div class="back__lockup">
      <span class="brand-dot" aria-hidden="true"></span>
      <span class="brand-name">brightvale</span>
    </div>
    <div class="back__web">
      <span>www.brightvale.example</span>
      <span class="back__rule" aria-hidden="true"></span>
    </div>
  </section>
</main>
</body>
</html>
```